Audit/Compliance company needs Business Card Template

We are after a Business Card Template that we can modify internally to update details as people change positions.
We are an Australian based company specalising in Auditing and Quality/OHS systems development. - See www.brimfieldreview.com.au for more information
We would like the desings to be based around our logo and colours assocaited with it (attached for your information) however we are very open as to how the cards are designed.
We are looking for something quite edgy and mordern but it must have a professional/compliance feel to it (if possible).
The main details we would like to include within the card template are:
Name
Position Title
Postal Address
Phone Number
Mobile Number
Email Address
Website
The cards will be printed through lanterly press on Glossy paper so it should reflect the requirements below
Full Bleed Size (starting document size)
90 x 52 mm
1062 x 615 pixels
Document Trim Size (final size after being cut)
87 x 49 mm
1028 x 579 pixels
Resolution
300 DPI

```html
<!DOCTYPE html>
<html lang="en">
<head>
<meta charset="utf-8">
<title>Brimfield Review – Business Card</title>
<link rel="stylesheet" href="https://fonts.googleapis.com/css2?family=Noto+Serif:wght@400&display=swap">
<style>
  :root {
    --page: #ffffff;
    --card-centre: #f7f8f8;
    --card-edge: #eceeef;
    --card-border: #4a4a4a;
    --ink: #454545;
    --rule: #cfd1d2;
    --chevron: #5a5a5a;
  }
  * { margin: 0; padding: 0; box-sizing: border-box; }
  html, body {
    width: 890px;
    height: 1200px;
    overflow: hidden;
    background: var(--page);
  }
  body {
    position: relative;
    font-family: "Noto Serif", serif;
    color: var(--ink);
  }
  .card {
    position: absolute;
    left: 10px;
    width: 879px;
    height: 508px;
    border: 1px solid var(--card-border);
    background: radial-gradient(ellipse at 50% 50%, var(--card-centre) 0%, var(--card-edge) 75%);
  }
  .card--front { top: 70px; }
  .card--back { top: 621px; }

  .chevron {
    position: absolute;
    left: 0;
    top: 0;
    width: 879px;
    height: 508px;
  }

  .brand-name {
    position: absolute;
    left: 52px;
    top: 233px;
    font-size: 34px;
    line-height: 1;
    letter-spacing: 0.5px;
    text-transform: uppercase;
    white-space: nowrap;
  }

  .holder {
    position: absolute;
    left: 600px;
    width: 270px;
    text-align: center;
  }
  .holder__name { top: 78px; font-size: 31px; }
  .holder__role { top: 124px; font-size: 23px; }

  .contact-line {
    position: absolute;
    left: 646px;
    font-size: 23px;
    white-space: nowrap;
  }
  .contact-line--phone { top: 383px; }
  .contact-line--mobile { top: 426px; }

  .back-detail {
    position: absolute;
    left: 0;
    width: 879px;
    text-align: center;
    font-size: 23px;
    white-space: nowrap;
  }
  .back-detail--email { top: 148px; }
  .back-detail--web { top: 239px; }
  .back-detail--address { top: 326px; }

  .back-rule {
    position: absolute;
    height: 1px;
    background: var(--rule);
  }
  .back-rule--short { top: 204px; left: 246px; width: 387px; }
  .back-rule--long { top: 298px; left: 165px; width: 547px; }
</style>
</head>
<body>
  <section class="card card--front">
    <svg class="chevron" viewBox="0 0 879 508" aria-hidden="true">
      <polyline points="493,38 701,258 479,471" fill="none" stroke="var(--chevron)" stroke-width="1"/>
    </svg>

    <div class="brand-name">Brimfield Review</div>

    <div class="holder holder__name">Dorran Keswick</div>
    <div class="holder holder__role">Manager</div>

    <div class="contact-line contact-line--phone">Phone number</div>
    <div class="contact-line contact-line--mobile">Mobile number</div>
  </section>

  <section class="card card--back">
    <div class="back-detail back-detail--email">office@brimfieldreview.com.au</div>
    <div class="back-rule back-rule--short"></div>
    <div class="back-detail back-detail--web">www.brimfieldreview.com.au</div>
    <div class="back-rule back-rule--long"></div>
    <div class="back-detail back-detail--address">Unit 14, Carrow Lane, Sydney, Australia</div>
  </section>
</body>
</html>
```